Simple Business Card Design for Tavlo

Job:

Make a very simple, minimalist business card design with my details including adjusted logo. One side to be white (with logo & text). Other side to be yellow - try plain or with logo (or part of logo eg Z). Need business card to have continuity with website.

Logo:
Our logo is made from a free download font website:
http://www.typewell.net/search.php?q=rubber
but the spacing/kerning needs correcting/adjusting as the font spaces unevenly between letters (see attached files). Need logo to be very crisp/sharp when printed.

Printing:
We will be using Plika.com so the design needs to conform to their requirements, see here:

http://uk.plika.com/products/luxe/business-cards.html (scroll down for dimensions and guidelines)

Design:

must say "plant-based food consulting" underneath logo or somewhere
no address needed in contact section
sharp corners (not rounded)
one side white, one side yellow

name: Rosalind Whitcombe
1xmobile number: +44 7700900463
1xtwiiter: @brimcounsel
website address www.orchardtable.com
email address brim@orchardtable.com

Should be easy quick job, prompt + detailed feedback given, am online in UK 9am-10pm for next 3 days. Website is www.orchardtable.com

Industry/Entity Type

Business

Requirements
Must have
• The logo must be corrected. The kerning is not right.

Please use a warm-grey for text

Please submit in matt format, we will be printing matt finish.

Should not have
• Avoid using banners or curvy highlights

Please avoid using black

Please avoid submitting in gloss finish

```html
<!DOCTYPE html>
<html lang="en">
<head>
<meta charset="utf-8">
<title>Brim – Business Card</title>
<link rel="stylesheet" href="https://fonts.googleapis.com/css2?family=Cinzel:wght@400;700&display=swap">
<style>
  :root {
    --backdrop: #e8e8e7;
    --paper-white: #fbfbfa;
    --paper-yellow: #f3e76c;
    --brand-yellow: #ebdc57;
    --warm-grey: #5f5b57;
  }
  * { margin: 0; padding: 0; box-sizing: border-box; }
  html, body { width: 1200px; height: 720px; overflow: hidden; }
  body {
    background: var(--backdrop);
    position: relative;
    font-family: "Cinzel", serif;
  }
  .card {
    position: absolute;
    top: 242px;
    width: 420px;
    height: 240px;
  }
  .card--front { left: 147px; background: var(--paper-white); }
  .card--back  { left: 633px; background: var(--paper-yellow); }

  .wordmark {
    font-family: "Cinzel", serif;
    font-weight: 700;
    letter-spacing: 0.04em;
    line-height: 1;
    position: absolute;
  }
  .card--front .wordmark {
    color: var(--brand-yellow);
    font-size: 56px;
    left: 40px;
    top: 92px;
  }
  .divider {
    position: absolute;
    left: 210px;
    top: 82px;
    width: 1px;
    height: 74px;
    background: var(--brand-yellow);
  }
  .holder-name {
    position: absolute;
    left: 231px;
    top: 80px;
    font-size: 11.5px;
    font-weight: 700;
    color: var(--brand-yellow);
    font-variant: small-caps;
    letter-spacing: 0.02em;
  }
  .contact-list {
    position: absolute;
    left: 233px;
    top: 110px;
    list-style: none;
    color: var(--brand-yellow);
    font-size: 8px;
    line-height: 12px;
    text-transform: uppercase;
  }
  .contact-list li { display: flex; align-items: center; gap: 7px; }
  .contact-icon { width: 8px; height: 8px; flex: none; fill: var(--brand-yellow); }

  .card--back .wordmark {
    color: var(--warm-grey);
    font-size: 68px;
    left: 0; right: 0;
    text-align: center;
    top: 72px;
  }
  .tagline {
    position: absolute;
    left: 0; right: 0;
    top: 151px;
    text-align: center;
    font-size: 11.5px;
    font-weight: 700;
    color: var(--warm-grey);
    letter-spacing: 0.01em;
  }
</style>
</head>
<body>
  <section class="card card--front" aria-label="Card front">
    <div class="wordmark">BRIM</div>
    <div class="divider"></div>
    <p class="holder-name">Rosalind Whitcombe</p>
    <ul class="contact-list">
      <li>
        <svg class="contact-icon" viewBox="0 0 8 8" aria-hidden="true"><path d="M1 1.2 C1 0.8 1.3 0.6 1.6 0.6 H2.6 L3.1 2.2 L2.3 2.8 C2.8 4 3.9 5.1 5.2 5.6 L5.8 4.8 L7.4 5.3 V6.4 C7.4 6.8 7.1 7.2 6.7 7.2 C3.5 7.2 1 4.5 1 1.2 Z"/></svg>
        +44 7700900463
      </li>
      <li>
        <svg class="contact-icon" viewBox="0 0 8 8" aria-hidden="true"><path d="M0.5 1.5 H7.5 V6.5 H0.5 Z M0.5 1.5 L4 4.3 L7.5 1.5" fill="none" stroke="currentColor" style="stroke:var(--brand-yellow)" stroke-width="0.9"/></svg>
        brim@orchardtable.com
      </li>
      <li>
        <svg class="contact-icon" viewBox="0 0 8 8" aria-hidden="true"><rect x="1" y="1" width="6" height="6"/></svg>
        @brimcounsel
      </li>
      <li>
        <svg class="contact-icon" viewBox="0 0 8 8" aria-hidden="true"><rect x="0.8" y="1" width="6.4" height="4.4" fill="none" style="stroke:var(--brand-yellow)" stroke-width="0.9"/><rect x="2.5" y="6.3" width="3" height="0.9"/></svg>
        www.orchardtable.com
      </li>
    </ul>
  </section>

  <section class="card card--back" aria-label="Card back">
    <div class="wordmark">BRIM</div>
    <p class="tagline">PLANT-BASED FOOD CONSULTING</p>
  </section>
</body>
</html>
```